redesign of my existing custom website into Wordpress based website

I need someone to redesign my current website into something more classy, simplistic, modern and on trend. I would like it set up on Wordpress in a way thats easy for me to make my own additions to blogs/price changes and promotion banners. I will also need a page that is password protected so members can login and have access to all my training videos and resources.
website is www.tidewellmamas.com.au

Target Market(s)

new mums

Industry/Entity Type

Fitness

Coding

Coded - Design and coding required

Number of Pages Required

5+ page

Colors
33a6d7

Requirements
Must have
• chic, modern, stylish and simplistic.
• a call to action above the page fold
• mobile friendly conversion
• a pop up message as soon as someone enters my sight offering my free report
• a members page that is password protected containing 3 youtube videos and 6 pdf attachments as resources
• a home page
• a contact us page
• an about us page
• a blog page
• a store page
Nice to have
• some examples of my peers websites that I like:
• www.norapellwick.com
• https://www.9qlr.com
• https://41bytedgarth.com
Should not have
• anything gimmicky

```html
<!DOCTYPE html>
<html lang="en">
<head>
<meta charset="utf-8">
<title>Tidewell Mamas – Login</title>
<link rel="stylesheet" href="https://fonts.googleapis.com/css2?family=Lato:wght@400;700;900&family=Open+Sans:wght@400;600&display=swap">
<style>
  :root {
    --pink: #f2137e;
    --ink: #1f1f1f;
    --card-head: #262626;
    --field-border: #b9b9b9;
    --placeholder: #6a6a6a;
    --muted: #4a4a4a;
    --white: #ffffff;
    --hero-dark: #2c2a29;
    --hero-warm: #4a4541;
  }
  * { box-sizing: border-box; margin: 0; padding: 0; }
  html, body { width: 1200px; height: 694px; overflow: hidden; }
  body { position: relative; background: var(--white); font-family: "Lato", Arial, sans-serif; color: var(--ink); }

  .top-rule { position: absolute; left: 0; top: 0; width: 1200px; height: 3px; background: var(--pink); }

  .site-header { position: absolute; left: 0; top: 3px; width: 1200px; height: 89px; background: var(--white); }
  .brand { position: absolute; left: 127px; top: 30px; display: flex; align-items: center; gap: 8px;
    font-family: "Lato", Arial, sans-serif; font-weight: 700; font-size: 19px; color: var(--ink); letter-spacing: .2px; }
  .brand-dot { width: 26px; height: 26px; border-radius: 50%; background: var(--ink); }

  .main-nav { position: absolute; left: 368px; top: 37px; display: flex; gap: 36px; }
  .main-nav a { font-weight: 700; font-size: 14.5px; color: var(--ink); text-decoration: none; letter-spacing: .2px; }

  .btn-login-nav { position: absolute; left: 903px; top: 26px; width: 96px; height: 35px; border: 1px solid #b3b3b3;
    border-radius: 18px; display: flex; align-items: center; justify-content: center; gap: 6px;
    font-weight: 700; font-size: 14px; color: var(--ink); }
  .btn-login-nav svg { width: 10px; height: 12px; }
  .btn-join-nav { position: absolute; left: 1006px; top: 26px; width: 95px; height: 35px; border-radius: 18px;
    background: var(--pink); color: var(--white); display: flex; align-items: center; justify-content: center;
    font-weight: 700; font-size: 14px; }

  .hero { position: absolute; left: 0; top: 92px; width: 1200px; height: 602px;
    background: radial-gradient(ellipse at 78% 18%, #6b625a 0%, transparent 40%),
                linear-gradient(180deg, var(--hero-warm) 0%, var(--hero-dark) 55%, #23232f 100%); }

  .login-card { position: absolute; left: 369px; top: 191px; width: 462px; height: 392px; background: var(--white);
    box-shadow: 0 4px 14px rgba(0,0,0,.35); }
  .login-card__head { position: relative; margin: 3px 3px 0; height: 53px; background: var(--card-head);
    display: flex; align-items: center; justify-content: center; }
  .login-card__head h1 { font-weight: 700; font-size: 24px; color: var(--white); letter-spacing: .5px; }
  .login-card__pointer { position: absolute; left: 50%; bottom: -15px; transform: translateX(-50%); width: 40px; height: 15px; }

  .field { position: absolute; left: 24px; width: 414px; height: 47px; border: 1px solid var(--field-border);
    font-family: "Open Sans", Arial, sans-serif; font-size: 14px; color: var(--placeholder);
    display: flex; align-items: center; padding-left: 15px; letter-spacing: .3px; }
  .field--email { top: 106px; }
  .field--password { top: 176px; }

  .form-row { position: absolute; left: 24px; top: 252px; width: 414px; display: flex; justify-content: space-between;
    align-items: center; font-family: "Open Sans", Arial, sans-serif; font-size: 14px; color: var(--muted); }
  .remember { display: flex; align-items: center; gap: 12px; }
  .checkbox { width: 21px; height: 18px; border: 1px solid #b9b9b9; border-radius: 2px; background: #fbfbfb; }

  .btn-submit { position: absolute; left: 24px; top: 302px; width: 146px; height: 49px; border-radius: 25px;
    background: var(--pink); color: var(--white); display: flex; align-items: center; justify-content: center;
    font-weight: 900; font-size: 17px; letter-spacing: .5px; }
</style>
</head>
<body>
  <div class="top-rule"></div>

  <header class="site-header">
    <div class="brand"><span class="brand-dot"></span>Tidewell Mamas</div>
    <nav class="main-nav">
      <a href="#">HOME</a>
      <a href="#">PROGRAM</a>
      <a href="#">BLOG</a>
      <a href="#">FAQ</a>
      <a href="#">ABOUT</a>
      <a href="#">CONTACT</a>
    </nav>
    <div class="btn-login-nav">
      <svg viewBox="0 0 10 12" aria-hidden="true"><path d="M2.5 5V3.5a2.5 2.5 0 0 1 5 0V5" fill="none" stroke="#f2137e" stroke-width="1.6"/><rect x="1" y="5" width="8" height="7" rx="1" fill="#f2137e"/></svg>
      LOGIN
    </div>
    <div class="btn-join-nav">JOIN</div>
  </header>

  <section class="hero" role="img" aria-label="Dimmed photo of a mother exercising on a mat in her living room while her baby plays beside her"></section>

  <div class="login-card">
    <div class="login-card__head">
      <h1>LOGIN</h1>
      <svg class="login-card__pointer" viewBox="0 0 40 15" aria-hidden="true"><polygon points="0,0 40,0 20,15" fill="#262626"/></svg>
    </div>
    <div class="field field--email">EMAIL :</div>
    <div class="field field--password">PASSWORD :</div>
    <div class="form-row">
      <span class="remember"><span class="checkbox"></span>Remember Me</span>
      <span class="forgot">Forgot Password?</span>
    </div>
    <div class="btn-submit">LOGIN</div>
  </div>
</body>
</html>
```